Communication and Marketing agency needs a new presentation card

We are a group of communication and marketing agencies specialized in companies that are in the logistics and industrial sector. The head agency is TELVANO Grupo and the group consists of 4 agencies: TELVANO Media, TELVANO Digital, TELVANO Research and DifundeEnPantalla. We hace 4 offices in Spain (Madrid, Barcelona, Valencia and Murcia). We are looking for a clean and attractive design that transmits our experience, brand presence in the market and knowledge to those who receive the card.It has to maintain the colors of the logo that is attached.
Target Market(s)
logistics and industrial sector
Marketing department
Contact Information for Business Card
Clean and attractive design

```html
<!DOCTYPE html>
<html lang="en">
<head>
<meta charset="utf-8">
<title>DifundeEnPantalla – Business Card</title>
<link href="https://fonts.googleapis.com/css2?family=Questrial&display=swap" rel="stylesheet">
<style>
  :root {
    --stage: #232122;
    --brand-red: #a3161f;
    --brand-red-dark: #8c1119;
    --ribbon-grey: #7a7a7a;
    --ribbon-fold: #4a4a4a;
    --paper: #ffffff;
    --paper-shade: #dcdcdc;
    --band-grey: #6a6a6a;
  }
  * { margin: 0; padding: 0; box-sizing: border-box; }
  html, body { width: 991px; height: 1200px; overflow: hidden; background: var(--stage); }
  body { font-family: "Questrial", sans-serif; }

  .canvas {
    width: 991px; height: 1200px;
    display: flex; flex-direction: column; align-items: center; justify-content: center;
    gap: 100px;
  }
  .card {
    width: 800px; height: 457px; position: relative; overflow: hidden;
    box-shadow: 0 10px 30px rgba(0,0,0,.45);
  }

  /* Shared wordmark: two fixed lines, never wraps inside a word */
  .wordmark { line-height: 1.02; letter-spacing: 1px; text-align: left; }
  .wordmark__line { display: block; white-space: nowrap; }

  /* Contact side */
  .card__identity {
    position: absolute; left: 0; top: 0;
    width: 400px; height: 100%;
    background: radial-gradient(circle at 45% 45%, var(--paper) 30%, var(--paper-shade) 100%);
    display: flex; align-items: center; justify-content: center;
  }
  .wordmark--card { color: var(--brand-red); font-size: 54px; }
  .card__details {
    position: absolute; left: 400px; top: 0;
    width: 400px; height: 100%;
    background: linear-gradient(160deg, var(--brand-red) 0%, var(--brand-red-dark) 100%);
  }
  .ribbon {
    position: absolute; top: 85px; left: 381px; width: 419px; height: 72px;
    background: var(--ribbon-grey); color: var(--paper);
    padding: 8px 0 0 112px;
  }
  .ribbon::after {
    content: ""; position: absolute; left: 0; bottom: -14px;
    border-top: 14px solid var(--ribbon-fold); border-left: 19px solid transparent;
  }
  .ribbon__name { font-size: 30px; line-height: 1.05; white-space: nowrap; }
  .ribbon__title { font-size: 22px; line-height: 1.1; }

  .contact-list { position: absolute; top: 178px; left: 467px; list-style: none; color: var(--paper); }
  .contact-list li { display: flex; align-items: flex-start; font-size: 20px; line-height: 1.3; margin-bottom: 14px; white-space: nowrap; }
  .contact-list svg { width: 18px; height: 18px; margin: 4px 14px 0 0; flex: none; }

  /* Brand side */
  .card--brand { background: var(--paper); }
  .card__hero {
    height: 357px;
    background: linear-gradient(160deg, var(--brand-red) 0%, var(--brand-red-dark) 100%);
    display: flex; align-items: center; justify-content: center;
  }
  .wordmark--hero { color: var(--paper); font-size: 76px; }
  .agency-band {
    height: 100px; display: flex; align-items: center; justify-content: space-around;
    background: linear-gradient(var(--paper), #ececec);
  }
  .agency { font-size: 19px; letter-spacing: .5px; white-space: nowrap; }
  .agency--grey { color: var(--band-grey); }
  .agency--red { color: var(--brand-red); }
</style>
</head>
<body>
<main class="canvas">
  <section class="card card--contact" aria-label="Contact side of business card">
    <div class="card__identity">
      <p class="wordmark wordmark--card"><span class="wordmark__line">DifundeEn</span><span class="wordmark__line">Pantalla</span></p>
    </div>
    <div class="card__details"></div>
    <div class="ribbon">
      <p class="ribbon__name">Marco Lindell</p>
      <p class="ribbon__title">Director</p>
    </div>
    <ul class="contact-list">
      <li>
        <svg viewBox="0 0 18 18" fill="none" stroke="#fff" stroke-width="2"><rect x="5" y="2" width="9" height="14" rx="2"/><line x1="8" y1="13" x2="11" y2="13"/></svg>
        0600 47 58210
      </li>
      <li>
        <svg viewBox="0 0 18 18" fill="#fff"><path d="M2 4h14v10H2z"/><path d="M2 4l7 6 7-6" fill="none" stroke="#a3161f" stroke-width="1.5"/></svg>
        info@difundeenpantalla.es
      </li>
      <li>
        <svg viewBox="0 0 18 18" fill="none" stroke="#fff" stroke-width="1.6"><circle cx="9" cy="9" r="7"/><line x1="2" y1="9" x2="16" y2="9"/><ellipse cx="9" cy="9" rx="3" ry="7"/></svg>
        www.difundeenpantalla.es
      </li>
      <li>
        <svg viewBox="0 0 18 18" fill="none" stroke="#fff" stroke-width="1.6"><path d="M9 2a4 4 0 0 1 4 4c0 3-4 7-4 7S5 9 5 6a4 4 0 0 1 4-4z"/><line x1="2" y1="16" x2="16" y2="16"/></svg>
        <span>214/36 calle norte,<br>valencia 46001</span>
      </li>
    </ul>
  </section>

  <section class="card card--brand" aria-label="Brand side of business card">
    <div class="card__hero">
      <p class="wordmark wordmark--hero"><span class="wordmark__line">DifundeEn</span><span class="wordmark__line">Pantalla</span></p>
    </div>
    <div class="agency-band">
      <span class="agency agency--grey">TELVANO Digital</span>
      <span class="agency agency--red">TELVANO Media</span>
      <span class="agency agency--red">TELVANO Grupo</span>
      <span class="agency agency--grey">TELVANO Research</span>
    </div>
  </section>
</main>
</body>
</html>
```